BorrowNest Website design, we are a home loan / lending company

We are a finance broking company that can do mortgages / home loans, Car Loans, Commercial Loans, SMSF Loans, Business Loans, Personal Loans
We are looking for a simple website, not too busy, easy to navigate, something that prompts customers to action or call us.
I like the simplicity of the following websites:
https://www.velkarafinance.com.au/ - I like this website front page. I was thinking I have my logo, the one with the black background appear , then the toolbar at the top perhaps?
https://trevix.com.au/business-loans# - on this page there are images under finance that works for you that I like that concept.
https://dunmerel.com.au/contact/ - I like the Make an Appointment page
https://trevix.com.au/about-us - Simple but effective page design

Target Market(s)

Home Loan Customer

Industry/Entity Type

Finance / Home Loans

Coding

Coded - Design and coding required

Number of Pages Required

5+ page

Font styles to use
Serif

Colors
0094D4
00A9DD
6FCCEA
C7EBF8
E9F6FB

Requirements
Must have
• The following Heading s - Contact Us, About Us, Our People, Make an Appointment, Loan Options, Calculators, Reviews. I want to use the Logo colours I have in the zip files I uploaded.
Nice to have
• Simple clean design

```html
<!DOCTYPE html>
<html lang="en">
<head>
<meta charset="utf-8">
<title>BorrowNest – Home Loans &amp; Lending</title>
<link href="https://fonts.googleapis.com/css2?family=Poppins:wght@400;500;600;700&display=swap" rel="stylesheet">
<style>
:root{
  --blue:#0094D4;
  --cyan:#00A9DD;
  --sky:#6FCCEA;
  --ice:#C7EBF8;
  --mist:#E9F6FB;
  --ink:#262a30;
  --text:#4a4f57;
  --navy:#0b1631;
  --people:#2f8ee0;
  --accent:#1f8fe6;
  --star:#f26b21;
}
*{box-sizing:border-box;margin:0;padding:0}
html,body{width:1200px;height:4348px;overflow:hidden}
body{font-family:"Poppins",sans-serif;color:var(--text);background:#fff;position:relative}
.abs{position:absolute}
a{color:inherit;text-decoration:none}

/* header */
.site-header{position:absolute;left:0;top:0;width:1200px;height:122px;background:#fff;z-index:3}
.brand{position:absolute;left:111px;top:36px;font-weight:600;font-size:38px;color:var(--ink);letter-spacing:-.5px;line-height:46px}
.topbar{position:absolute;left:422px;top:0;width:667px;height:46px;background:var(--cyan);clip-path:polygon(28px 0,100% 0,100% 100%,0 100%);display:flex;align-items:center;padding-left:42px;gap:30px;font-size:14px;color:#fff}
.topbar span{display:flex;align-items:center;gap:8px}
.topbar .cta{position:absolute;right:0;top:0;height:46px;width:228px;background:#22c1f0;clip-path:polygon(20px 0,100% 0,100% 100%,0 100%);display:flex;align-items:center;justify-content:center;font-weight:600;font-size:15px}
.main-nav{position:absolute;top:75px;left:0;font-size:15px;color:var(--ink);font-weight:500}
.main-nav a{position:absolute;white-space:nowrap}
.main-nav .active{color:var(--cyan)}
.main-nav .dot{position:absolute;left:16px;top:-14px;width:10px;height:10px;border-radius:50%;border:2px solid var(--cyan)}

/* hero */
.hero{position:absolute;left:0;top:122px;width:1200px;height:685px;background:linear-gradient(90deg,#eef1f4 0%,#e3e8ed 40%,#c9d1da 100%);overflow:hidden}
.hero-photo{position:absolute;left:280px;top:0;width:920px;height:685px;background:radial-gradient(ellipse at 75% 40%,#3e5680 0%,#7889a3 35%,rgba(220,226,232,0) 70%)}
.hero-copy{position:absolute;left:111px;top:92px;width:500px}
.hero-copy .welcome{font-size:44px;font-weight:400;color:var(--ink);line-height:54px}
.hero-copy .title{font-size:84px;font-weight:600;color:var(--ink);line-height:96px;letter-spacing:-1.5px;margin-top:2px}
.hero-copy p{font-size:15px;line-height:27px;color:#333;margin-top:18px;width:470px}
.btn{display:flex;align-items:center;padding-left:16px;height:46px;width:144px;color:#fff;font-weight:600;font-size:15px;background:linear-gradient(90deg,var(--blue),var(--cyan) 70%,var(--sky));clip-path:polygon(0 0,100% 0,calc(100% - 28px) 100%,0 100%)}
.hero .btn{position:absolute;left:111px;top:346px;width:228px;height:38px;font-size:15px}
.social-rail{position:absolute;left:41px;top:218px;width:22px;display:flex;flex-direction:column;align-items:center;gap:14px}
.social-rail i{display:block;width:12px;height:12px;border-radius:50%;background:#3a4250}
.social-rail i.first{width:22px;height:22px;border:2px solid var(--cyan);background:none}
.social-rail .line{width:1px;height:80px;background:#7b838f}
.social-rail .scroll{writing-mode:vertical-rl;transform:rotate(180deg);font-size:9px;letter-spacing:1px;color:#3a4250}

/* section heads */
.section-title{font-size:36px;font-weight:600;color:var(--ink);line-height:44px}
.section-title em{font-style:normal;color:var(--accent)}
.body-copy{font-size:14.5px;line-height:25.7px;text-align:justify}

/* about */
.about-photo{position:absolute;left:140px;top:906px;width:400px;height:380px;border-radius:50%;background:radial-gradient(circle at 35% 40%,#44587c,#17223d 75%);box-shadow:0 14px 28px rgba(0,0,0,.12)}
.about-copy{position:absolute;left:599px;top:888px;width:488px}
.about-copy .body-copy{margin-top:18px}
.about-copy .btn{margin-top:22px}

/* people */
.people{position:absolute;left:0;top:1381px;width:1200px;height:643px;background:linear-gradient(90deg,#3d9ae6,#2f8ee0);overflow:hidden}
.people-photo{position:absolute;left:560px;top:0;width:640px;height:643px;background:radial-gradient(ellipse at 55% 45%,#1f6fc2 0%,#3087da 45%,rgba(47,142,224,0) 75%)}
.people-copy{position:absolute;left:111px;top:112px;width:488px;color:#fff}
.people-copy .section-title{color:#fff}
.people-copy .body-copy{margin-top:22px;color:#eaf4fd}
.btn-outline{display:block;margin-top:34px;width:142px;height:45px}
.btn-outline svg{display:block}

/* loans */
.loan-art{position:absolute;left:76px;top:2093px;width:515px;height:456px}
.loan-copy{position:absolute;left:630px;top:2155px;width:457px}
.loan-copy .body-copy{margin-top:16px}
.loan-copy .btn{margin-top:38px}

/* reviews */
.reviews{position:absolute;left:0;top:2638px;width:1200px;height:632px;background:linear-gradient(180deg,#eef2f6,#f4f7fa)}
.reviews-head{position:absolute;top:76px;width:1200px;text-align:center}
.reviews-head p{font-size:12px;margin-top:6px;color:#444}
.card{position:absolute;top:198px;width:297px;height:349px;background:#fff;border-top:3px solid var(--sky);box-shadow:0 6px 20px rgba(30,60,100,.08);padding:26px 26px 0}
.card.mid{border-top-color:var(--accent)}
.card .quote{font-size:54px;line-height:40px;color:var(--cyan);font-weight:700;height:34px;overflow:hidden}
.card .stars{color:var(--star);font-size:17px;letter-spacing:2px;margin-top:6px}
.card .said{font-size:13.5px;line-height:27px;color:#444;margin-top:10px}
.card hr{border:0;border-top:1px solid #e6e9ee;margin-top:24px}
.card .who{display:flex;align-items:center;gap:14px;margin-top:18px}
.card .avatar{width:56px;height:56px;border-radius:50%;background:linear-gradient(135deg,#5d6f88,#2a3550)}
.card .who b{display:block;font-size:16.5px;font-weight:600;color:var(--ink)}
.card .who small{font-size:11.5px;color:#666}

/* contact */
.contact-photo{position:absolute;left:127px;top:3351px;width:455px;height:506px;border-radius:48% 52% 44% 56%/40% 40% 60% 60%;background:radial-gradient(circle at 55% 55%,#6fccea 0%,#9ed9ee 35%,#c9cfd6 70%,#eef0f2 100%)}
.contact-form{position:absolute;left:599px;top:3364px;width:486px}
.field{position:absolute;background:#fff;box-shadow:0 3px 14px rgba(20,40,70,.09);font-size:12.5px;color:#555;padding:17px 20px}
.contact-form .btn{position:absolute;left:0;top:380px;width:144px;height:47px}

/* footer */
.site-footer{position:absolute;left:0;top:3942px;width:1200px;height:406px;background:var(--navy);color:#fff}
.site-footer .brand{left:111px;top:120px;color:#fff;font-size:36px}
.foot-social{position:absolute;left:114px;top:205px;display:flex;gap:16px}
.foot-social i{display:block;width:36px;height:36px;border-radius:50%;border:1.5px solid #fff}
.foot-col{position:absolute;top:74px}
.foot-col h4{font-size:17px;font-weight:600;letter-spacing:.3px;margin-bottom:14px}
.foot-col a{display:block;font-size:14.5px;line-height:26.5px;color:#e4e9f2}
.contact-item{display:flex;gap:14px;align-items:flex-start;font-size:14.5px;line-height:24px;margin-bottom:26px}
.contact-item .ic{flex:none;width:38px;height:38px;border-radius:50%;background:var(--accent);display:flex;align-items:center;justify-content:center}
.copyright{position:absolute;left:0;top:360px;width:1200px;text-align:center;font-size:14px;color:#e4e9f2}
</style>
</head>
<body>

<header class="site-header">
  <div class="brand">BorrowNest</div>
  <div class="topbar">
    <span><svg width="15" height="15" viewBox="0 0 24 24" fill="none" stroke="#fff" stroke-width="2"><path d="M22 16.9v3a2 2 0 0 1-2.2 2 19.8 19.8 0 0 1-8.6-3.1 19.5 19.5 0 0 1-6-6A19.8 19.8 0 0 1 2.1 4.2 2 2 0 0 1 4.1 2h3a2 2 0 0 1 2 1.7c.1 1 .4 1.9.7 2.8a2 2 0 0 1-.5 2.1L8 9.9a16 16 0 0 0 6 6l1.3-1.3a2 2 0 0 1 2.1-.4c.9.3 1.8.6 2.8.7a2 2 0 0 1 1.7 2z"/></svg>+1 (555) 014 2290</span>
    <span><svg width="17" height="13" viewBox="0 0 24 18" fill="none" stroke="#fff" stroke-width="2"><rect x="1" y="1" width="22" height="16" rx="1"/><path d="M1 2l11 8 11-8"/></svg>info@borrownest.com</span>
    <a class="cta" href="#contact">Make an Appointment</a>
  </div>
  <nav class="main-nav">
    <a class="active" style="left:414px">Home<span class="dot"></span></a>
    <a style="left:484px">Contact Us</a>
    <a style="left:591px">About Us</a>
    <a style="left:685px">Our People</a>
    <a style="left:793px">Loan Options</a>
    <a style="left:917px">Calculators</a>
    <a style="left:1026px">Reviews</a>
  </nav>
</header>

<section class="hero">
  <div class="hero-photo" role="img" aria-label="Photo of a smiling loan adviser in a navy suit holding a printed financial report beside a laptop"></div>
  <div class="social-rail">
    <i class="first"></i><i></i><i></i><i></i>
    <span class="line"></span>
    <span class="scroll">SCROLL DOWN</span>
    <svg width="14" height="14" viewBox="0 0 14 14" fill="none" stroke="#3a4250" stroke-width="1.5"><path d="M7 1v12M2 8l5 5 5-5"/></svg>
  </div>
  <div class="hero-copy">
    <div class="welcome">Welcome to</div>
    <div class="title">BorrowNest</div>
    <p>Lorem ipsum dolor sit amet, consectetur adipiscing elit, sed do eiusmod tempor incididunt ut labore et dolore magna aliqua.</p>
  </div>
  <a class="btn" href="#contact">Make an Appointment</a>
</section>

<section class="about">
  <div class="about-photo" role="img" aria-label="Round photo of a businessman reviewing documents at his desk"></div>
  <div class="about-copy">
    <h2 class="section-title">About <em>BorrowNest</em></h2>
    <p class="body-copy">Lorem ipsum dolor sit amet, consectetur adipiscing elit, sed do eiusmod tempor incididunt ut labore et dolore magna aliqua. Ut enim ad minim veniam, quis nostrud exercitation ullamco laboris nisi ut aliquip ex ea commodo consequat. Duis aute irure dolor in reprehenderit in voluptate velit esse cillum dolore eu fugiat nulla pariatur. Excepteur sint occaecat cupidatat non proident, sunt in culpa qui officia deserunt mollit anim id est laborum. Nemo enim ipsam voluptatem quia voluptas sit aspernatur aut odit aut fugit, sed quia consequuntur magni dolores eos qui ratione voluptatem sequi nesciunt.</p>
    <a class="btn" href="#">Learn More</a>
  </div>
</section>

<section class="people">
  <div class="people-photo" role="img" aria-label="Blue-toned photo of a smiling adviser in a suit in a bright office"></div>
  <div class="people-copy">
    <h2 class="section-title">Our People</h2>
    <p class="body-copy">Lorem ipsum dolor sit amet, consectetur adipiscing elit, sed do eiusmod tempor incididunt ut labore et dolore magna aliqua. Ut enim ad minim veniam, quis nostrud exercitation ullamco laboris nisi ut aliquip ex ea commodo consequat. Duis aute irure dolor in reprehenderit in voluptate velit esse cillum dolore eu fugiat nulla pariatur. Excepteur sint occaecat cupidatat non proident, sunt in culpa qui officia deserunt mollit anim id est laborum. Nemo enim ipsam voluptatem quia voluptas sit aspernatur aut odit aut fugit, sed quia consequuntur magni dolores eos qui ratione voluptatem sequi nesciunt.</p>
    <a class="btn-outline" href="#"><svg width="142" height="45" viewBox="0 0 142 45"><path d="M1 1H141L113 44H1Z" fill="none" stroke="#fff" stroke-width="1.5"/><text x="16" y="28" fill="#fff" font-family="Poppins, sans-serif" font-size="15" font-weight="600">Learn More</text></svg></a>
  </div>
</section>

<section class="loans">
  <svg class="loan-art" viewBox="0 0 515 456">
    <path d="M120 40C190-10 290 0 340 30 410 70 520 200 500 320 480 430 380 460 300 440 230 420 110 440 50 380-10 320 10 230 40 180 70 120 70 80 120 40Z" fill="#c7ebf8"/>
    <path role="img" aria-label="Photo of hands signing a loan document beside a calculator and laptop" d="M160 10C230-8 330 20 390 80 440 140 460 250 430 330 400 410 300 440 220 420 140 400 60 360 40 290 20 220 50 150 90 90 110 55 130 20 160 10Z" fill="#e6edf2"/>
  </svg>
  <div class="loan-copy">
    <h2 class="section-title">Loan <em>Options</em></h2>
    <p class="body-copy">Lorem ipsum dolor sit amet, consectetur adipiscing elit, sed do eiusmod tempor incididunt ut labore et dolore magna aliqua. Ut enim ad minim veniam, quis nostrud exercitation ullamco laboris nisi ut aliquip ex ea commodo consequat. Duis aute irure dolor in reprehenderit in voluptate velit esse cillum dolore eu fugiat nulla pariatur. Excepteur sint occaecat cupidatat non proident, sunt in culpa qui officia deserunt mollit anim id est laborum.</p>
    <a class="btn" href="#">Learn More</a>
  </div>
</section>

<section class="reviews">
  <div class="reviews-head">
    <h2 class="section-title">Customer <em>Review</em></h2>
    <p>Lorem ipsum dolor sit amet, consectetur adipiscing elit, sed do eiusmod tempor</p>
  </div>
  <article class="card" style="left:113px">
    <div class="quote">&ldquo;</div><div class="stars">★★★★★</div>
    <p class="said">Lorem ipsum dolor sit consectetur adipiscing elit, sed do eius tempor incididunt ut labore et dolor magna aliqua.</p>
    <hr><div class="who"><span class="avatar" role="img" aria-label="Customer portrait"></span><div><b>Marla Quenby</b><small>Lorem ipsum dolor</small></div></div>
  </article>
  <article class="card mid" style="left:451px">
    <div class="quote">&ldquo;</div><div class="stars">★★★★★</div>
    <p class="said">Lorem ipsum dolor sit consectetur adipiscing elit, sed do eius tempor incididunt ut labore et dolor magna aliqua.</p>
    <hr><div class="who"><span class="avatar" role="img" aria-label="Customer portrait"></span><div><b>Marla Quenby</b><small>Lorem ipsum dolor</small></div></div>
  </article>
  <article class="card" style="left:788px">
    <div class="quote">&ldquo;</div><div class="stars">★★★★★</div>
    <p class="said">Lorem ipsum dolor sit consectetur adipiscing elit, sed do eius tempor incididunt ut labore et dolor magna aliqua.</p>
    <hr><div class="who"><span class="avatar" role="img" aria-label="Customer portrait"></span><div><b>Marla Quenby</b><small>Lorem ipsum dolor</small></div></div>
  </article>
</section>

<section class="contact" id="contact">
  <div class="contact-photo" role="img" aria-label="Photo of a smiling woman sitting cross-legged with a laptop, giving a thumbs up"></div>
  <div class="contact-form">
    <h2 class="section-title">Contact <em>Us</em></h2>
    <div class="field" style="left:0;top:93px;width:235px;height:54px">First Name</div>
    <div class="field" style="left:252px;top:93px;width:234px;height:54px">Last Name</div>
    <div class="field" style="left:0;top:162px;width:235px;height:54px">Phone</div>
    <div class="field" style="left:252px;top:162px;width:234px;height:54px">Email</div>
    <div class="field" style="left:0;top:232px;width:486px;height:123px">Message</div>
    <a class="btn" href="#">submit</a>
  </div>
</section>

<footer class="site-footer">
  <div class="brand">BorrowNest</div>
  <div class="foot-social"><i></i><i></i><i></i><i></i></div>
  <div class="foot-col" style="left:422px">
    <h4>QUICK LINKS</h4>
    <a>Home</a><a>Contact Us</a><a>About Us</a><a>Our People</a><a>Loan Options</a><a>Calculators</a><a>Reviews</a>
  </div>
  <div class="foot-col" style="left:638px">
    <h4>COMPANY</h4>
    <a>Terms of Use</a><a>About Us</a><a>Privacy Policy</a><a>Practice</a>
  </div>
  <div class="foot-col" style="left:827px;width:280px">
    <h4>CONTACT US</h4>
    <div class="contact-item"><span class="ic"><svg width="16" height="18" viewBox="0 0 24 28" fill="#fff"><path d="M12 0a10 10 0 0 0-10 10c0 8 10 18 10 18s10-10 10-18A10 10 0 0 0 12 0zm0 14a4 4 0 1 1 0-8 4 4 0 0 1 0 8z"/></svg></span><span>Lorem ipsum dolor sit amet, consectetur adipiscing elit.</span></div>
    <div class="contact-item" style="align-items:center"><span class="ic"><svg width="17" height="17" viewBox="0 0 24 24" fill="#fff"><path d="M22 16.9v3a2 2 0 0 1-2.2 2 19.8 19.8 0 0 1-8.6-3.1 19.5 19.5 0 0 1-6-6A19.8 19.8 0 0 1 2.1 4.2 2 2 0 0 1 4.1 2h3a2 2 0 0 1 2 1.7c.1 1 .4 1.9.7 2.8a2 2 0 0 1-.5 2.1L8 9.9a16 16 0 0 0 6 6l1.3-1.3a2 2 0 0 1 2.1-.4c.9.3 1.8.6 2.8.7a2 2 0 0 1 1.7 2z"/></svg></span><span>+1 (555) 014 2290</span></div>
    <div class="contact-item" style="align-items:center"><span class="ic"><svg width="17" height="13" viewBox="0 0 24 18" fill="none" stroke="#fff" stroke-width="2"><rect x="1" y="1" width="22" height="16" rx="1"/><path d="M1 2l11 8 11-8"/></svg></span><span>info@borrownest.com</span></div>
  </div>
  <div class="copyright">©Copyrights 2022 BorrowNest &nbsp;|&nbsp; All Rights Reserved</div>
</footer>

</body>
</html>
```